Online business manager needs a website

I need a website designed and then coded. I am an online business manager serving a number of different industries providing administrative support to existing small businesses and helping solo practitioners get their new business up and running.

I didn't have a logo formally designed but have been using the attached avatar and wouldn't mind something that incorporated that.

The business doesn't have an official name, so I've just been using my name Lena Morvath, Online Business Manager or Lena Morvath, OBM. I've attached two documents that I have made previously for an example of content.

I would prefer the final site be in Wordpress.

Requirements
Must have
• A way to contact me, testimonials, list of services

```html
<!DOCTYPE html>
<html lang="en">
<head>
<meta charset="utf-8">
<title>Lena Morvath – Online Business Manager</title>
<link href="https://fonts.googleapis.com/css2?family=Poppins:ital,wght@0,300;0,400;0,500;0,600;0,700;1,400&display=swap" rel="stylesheet">
<style>
:root{
  --pink:#ff87b8;
  --ink:#111;
  --text:#333;
  --grey-bg:#f0f0f0;
  --light-bg:#f5f5f5;
  --frame-grey:#c4c4c4;
  --white:#fff;
}
*{box-sizing:border-box;margin:0;padding:0}
html,body{width:1200px;height:3930px;overflow:hidden}
body{font-family:"Poppins",sans-serif;color:var(--text);background:var(--white);position:relative}
section,header,footer{position:absolute;left:0;width:1200px}
.abs{position:absolute}
.btn{position:absolute;display:flex;align-items:center;justify-content:center;background:var(--pink);color:var(--white);font-weight:600;font-size:17px;letter-spacing:.5px;text-transform:uppercase}

/* hero */
.hero{top:0;height:701px;background:linear-gradient(100deg,#6f625c 0%,#8d8178 35%,#a79a8f 60%,#7d6b5e 100%)}
.hero-photo{position:absolute;inset:0;background:linear-gradient(100deg,rgba(70,62,58,.55) 0%,rgba(90,80,75,.3) 45%,rgba(120,95,75,.15) 70%,rgba(60,50,45,.3) 100%)}
.hero-shade{position:absolute;left:0;top:0;width:1200px;height:130px;background:linear-gradient(rgba(0,0,0,.8),rgba(0,0,0,0))}
.brand{left:75px;top:26px;color:var(--white)}
.brand-name{font-size:42px;font-weight:700;line-height:1.1}
.brand-tag{font-size:20px;font-style:italic;font-weight:400}
.nav{left:494px;top:48px;display:flex;gap:40px;font-size:17px;font-weight:500;color:var(--white)}
.nav .active{color:var(--pink)}
.hero-title{left:72px;top:245px;font-size:96px;font-weight:700;color:var(--white);line-height:1.1}
.hero-text{left:75px;top:358px;width:480px;font-size:21px;line-height:34px;color:var(--white)}
.dots{left:75px;top:654px;display:flex;gap:12px}
.dots span{width:11px;height:11px;border-radius:50%;background:#111}
.dots span:first-child{background:var(--white)}

/* about */
.about{top:701px;height:586px;background:var(--grey-bg)}
.frame-pink{left:75px;top:57px;width:328px;height:292px;border:4px solid var(--pink)}
.frame-grey{left:262px;top:237px;width:325px;height:290px;border:4px solid var(--frame-grey)}
.about-photo{left:104px;top:88px;width:455px;height:411px;background:linear-gradient(135deg,#b5316f,#d85d97 40%,#7e4a55 70%,#3f4a2e)}
.about h2{left:616px;top:80px;font-size:34px;font-weight:400;color:var(--ink)}
.about p{left:616px;top:138px;width:515px;font-size:15px;line-height:28.7px;color:var(--text)}

/* services */
.services{top:1287px;height:659px;background:var(--white)}
.sec-title{width:1200px;text-align:center;font-size:34px;font-weight:400;color:var(--ink)}
.service-card{top:131px;width:512px;height:450px}
.service-card .info{position:absolute;left:45px;top:265px;width:422px;height:185px;background:rgba(255,255,255,.9);text-align:center;padding-top:22px}
.service-card h3{color:var(--pink);font-size:23px;font-weight:600;margin-bottom:6px}
.service-card li{list-style:none;font-size:15.5px;line-height:27px;color:var(--ink)}
.arrow{width:24px;height:40px}

/* testimonials */
.testimonials{top:1946px;height:494px;background:var(--pink)}
.testimonials .sec-title{color:var(--white);top:72px}
.client-photo{left:138px;top:149px;width:262px;height:262px;border-radius:50%;border:4px solid #fbe9ef;background:linear-gradient(160deg,#6b8a3c,#5b6b40 50%,#3a2a2a)}
.testimonial-body{left:431px;top:176px;width:660px}
.quote{font-size:18px;font-style:italic;line-height:37px;color:var(--white)}
.quote-by{margin-top:12px;font-size:18px;font-weight:600;color:var(--white)}

/* rates */
.rates{top:2440px;height:642px;background:var(--light-bg)}
.plan{top:128px;width:328px;height:453px;background:var(--white);text-align:center}
.plan svg{position:absolute;left:0;top:0}
.plan h3{position:absolute;top:15px;width:100%;font-size:34px;font-weight:600;color:var(--white)}
.price{position:absolute;left:116px;top:70px;width:96px;height:96px;border-radius:50%;background:var(--white);border:4px solid var(--pink);display:flex;flex-direction:column;align-items:center;justify-content:center;color:var(--ink)}
.price b{font-size:30px;font-weight:500;line-height:1}
.price b sup{font-size:14px;vertical-align:top}
.price i{font-size:11.5px;line-height:1.2}
.plan ul{position:absolute;top:202px;width:100%;list-style:none}
.plan li{font-size:17px;line-height:43px;color:var(--ink)}
.plan .more{position:absolute;left:75px;top:380px;width:178px;height:46px;border:2px solid #555;border-radius:24px;display:flex;align-items:center;justify-content:center;font-size:16px;font-weight:500;color:#555}

/* contact */
.contact{top:3082px;height:464px;background:var(--pink)}
.contact h2{left:75px;top:55px;font-size:36px;font-weight:400;color:var(--white)}
.contact .sub{left:75px;top:114px;font-size:15px;color:var(--white)}
.field{position:absolute;background:var(--white);font-size:15px;color:#555;padding:14px 12px}
.submit{left:75px;top:346px;width:512px;height:50px;background:#000;color:var(--white);font-weight:600;font-size:18px;display:flex;align-items:center;justify-content:center}
.contact-photo{left:616px;top:0;width:584px;height:464px;background:linear-gradient(120deg,#5a4d45,#8a7a6a 40%,#d7a57a 65%,#3b3f4a)}

/* footer */
.site-footer{top:3546px;height:384px;background:#f7f7f7}
.fcol{top:68px}
.fcol h4{font-size:17px;font-weight:500;color:var(--pink);margin-bottom:10px;letter-spacing:.3px}
.fcol li{list-style:none;font-size:15px;line-height:33.5px;color:var(--ink)}
.social{display:flex;gap:20px;margin-top:14px}
.social span{width:20px;height:20px;background:#555;border-radius:3px}
.bottom-bar{left:0;top:312px;width:1200px;height:72px;border-top:1px solid #ddd;text-align:center;font-size:13px;color:#444;line-height:72px}
</style>
</head>
<body>

<header class="hero">
  <div class="hero-photo" role="img" aria-label="Photo of the business manager working at a laptop in an office"></div>
  <div class="hero-shade"></div>
  <div class="abs brand">
    <div class="brand-name">Lena Morvath</div>
    <div class="brand-tag">Online Business Manager</div>
  </div>
  <nav class="abs nav">
    <span class="active">Home</span><span>About Me</span><span>Services</span><span>Packages</span><span>Blog</span><span>Contact Me</span>
  </nav>
  <h1 class="abs hero-title">Lena Morvath</h1>
  <p class="abs hero-text">I am an online business manager serving a number of different industries providing administrative support.</p>
  <a class="btn" style="left:75px;top:485px;width:192px;height:62px">Read More</a>
  <div class="abs dots"><span></span><span></span><span></span><span></span></div>
</header>

<section class="about">
  <div class="abs frame-pink"></div>
  <div class="abs frame-grey"></div>
  <div class="abs about-photo" role="img" aria-label="Portrait of the business manager in front of flowering shrubs"></div>
  <h2 class="abs">ABOUT ME</h2>
  <p class="abs">Hi! I'm so excited that you have chosen to explore my portfolio. Helping businesses achieve their goals is my passion, and I'm thrilled that with my assistance you will have more time for your own passion project. I thrive while working independently, which means you can be confident when leaving tasks for me.<br>The type of work that lights me up is anything involving organization and/or spreadsheets. You need data analyzed that includes multiple nested if formulas? You have an overwhelming amount of email to sort through and appointments to book? I'm your gal!</p>
  <a class="btn" style="left:616px;top:449px;width:192px;height:62px">Read More</a>
</section>

<section class="services">
  <h2 class="abs sec-title" style="top:50px">OUR SERVICES OFFER</h2>
  <svg class="abs arrow" style="left:40px;top:337px" viewBox="0 0 24 40"><path d="M18 6 6 20l12 14" fill="none" stroke="#333" stroke-width="3"/></svg>
  <div class="abs service-card" style="left:75px">
    <div class="abs" style="inset:0;background:linear-gradient(135deg,#7c8a94,#d9dde2 45%,#e9e7e4 70%,#d19a70)" role="img" aria-label="Laptop beside a printed calendar"></div>
    <div class="info">
      <h3>VIRTUAL ASSISTANCE</h3>
      <ul><li>Calendar Management</li><li>Email Management</li><li>Light Graphic Design</li><li>Data Entry</li></ul>
    </div>
  </div>
  <div class="abs service-card" style="left:615px">
    <div class="abs" style="inset:0;background:linear-gradient(135deg,#8fc3dc,#e4e6e8 40%,#f2f2f2 65%,#7eb6d2)" role="img" aria-label="Calculator and invoice binder on a desk"></div>
    <div class="info">
      <h3>FINANCE MANAGEMENT</h3>
      <ul><li>Create Invoices</li><li>Track Receivables</li><li>Analyze Expenses</li><li>Year Over Year Analytics</li></ul>
    </div>
  </div>
  <svg class="abs arrow" style="left:1137px;top:337px" viewBox="0 0 24 40"><path d="M6 6l12 14L6 34" fill="none" stroke="#333" stroke-width="3"/></svg>
</section>

<section class="testimonials">
  <h2 class="abs sec-title">TESTIMONIALS</h2>
  <div class="abs client-photo" role="img" aria-label="Portrait of a client outdoors"></div>
  <div class="abs testimonial-body">
    <p class="quote">When it became apparent that a project would take more time than I had, Lena stepped up to take on the required research. She was thorough and timely; able to meet a last-minute 12-hour deadline. I would highly recommend Lena to assist with your next project.”</p>
    <div class="quote-by">Dana R. Owner, Northgate Roofing</div>
  </div>
</section>

<section class="rates">
  <h2 class="abs sec-title" style="top:52px">RATES AND PACKAGES</h2>
  <svg class="abs arrow" style="left:40px;top:347px" viewBox="0 0 24 40"><path d="M18 6 6 20l12 14" fill="none" stroke="#333" stroke-width="3"/></svg>
  <div class="abs plan" style="left:75px">
    <svg width="328" height="170"><polygon points="0,0 328,0 328,100 0,160" fill="var(--pink)"/></svg>
    <h3>Basic</h3>
    <div class="price"><b><sup>$</sup>40</b><i>Hour Rate</i></div>
    <ul><li>Sed ut perspiciatis unde</li><li>Omnis iste natus error</li><li>Sit voluptatem</li><li>Accusantium eos qui</li></ul>
    <div class="more">MORE INFO</div>
  </div>
  <div class="abs plan" style="left:437px">
    <svg width="328" height="170"><polygon points="0,0 328,0 328,100 0,160" fill="var(--pink)"/></svg>
    <h3>Standard</h3>
    <div class="price"><b><sup>$</sup>700</b><i>20 Hour<br>Month</i></div>
    <ul><li>Sed ut perspiciatis unde</li><li>Omnis iste natus error</li><li>Sit voluptatem</li><li>Accusantium eos qui</li></ul>
    <div class="more">MORE INFO</div>
  </div>
  <div class="abs plan" style="left:799px">
    <svg width="328" height="170"><polygon points="0,0 328,0 328,100 0,160" fill="var(--pink)"/></svg>
    <h3>Preminum</h3>
    <div class="price"><b style="font-size:24px"><sup>$</sup>2,400</b><i>80 Hour<br>Month</i></div>
    <ul><li>Sed ut perspiciatis unde</li><li>Omnis iste natus error</li><li>Sit voluptatem</li><li>Accusantium eos qui</li></ul>
    <div class="more">MORE INFO</div>
  </div>
  <svg class="abs arrow" style="left:1137px;top:347px" viewBox="0 0 24 40"><path d="M6 6l12 14L6 34" fill="none" stroke="#333" stroke-width="3"/></svg>
</section>

<section class="contact">
  <h2 class="abs">CONTACT ME</h2>
  <p class="abs sub">Sed ut perspiciatis unde omnis iste natus error sit</p>
  <div class="field" style="left:75px;top:160px;width:250px;height:50px">Name</div>
  <div class="field" style="left:75px;top:221px;width:250px;height:50px">Email Address</div>
  <div class="field" style="left:75px;top:282px;width:250px;height:50px">Phone No</div>
  <div class="field" style="left:337px;top:160px;width:250px;height:174px">Message</div>
  <div class="abs submit">SUBMIT</div>
  <div class="abs contact-photo" role="img" aria-label="Smiling portrait of the business manager on a city street"></div>
</section>

<footer class="site-footer">
  <div class="abs fcol" style="left:74px">
    <h4>QUICK LINKS</h4>
    <ul><li>Home</li><li>About Me</li><li>Services</li><li>Packages</li><li>Contact Us</li></ul>
  </div>
  <div class="abs fcol" style="left:284px">
    <h4>SERVICES</h4>
    <ul><li>Virtual Assistance</li><li>Social Media &amp; Content Management</li><li>Finance Management</li><li>Business Management</li></ul>
  </div>
  <div class="abs fcol" style="left:631px">
    <h4>GET IN TOUCH</h4>
    <ul><li>555.210.4487</li><li>lena.morvath@example.com</li></ul>
  </div>
  <div class="abs fcol" style="left:913px">
    <h4>FOLLOW US</h4>
    <div class="social" aria-label="Social profiles"><span></span><span></span><span></span><span></span></div>
  </div>
  <div class="abs bottom-bar">Copyright © 2023 Company Name. All Right Reserved</div>
</footer>

</body>
</html>
```